New Interrior Decoration company needs new website

We need a website for our new company specialising in interior decoration to residential and commercial markets.
We supply and install decorative and printed films for office and home decoration such as feature walls.
We would like to keep the design simple and clean.

Target Market(s)

Architects and interior designaers

Industry/Entity Type

It Company

Number of Pages Required

5+ page

Font styles to use
Sans Serif

Requirements
Must have
• Home page,
• Services/products page (split into commercial and residential)
• Gallery (split into commercial and residential)
• contact form and page
Nice to have
• Very clean and minimalistic design.

```html
<!DOCTYPE html>
<html lang="en">
<head>
<meta charset="utf-8">
<title>Vantage Interiors</title>
<link href="https://fonts.googleapis.com/css2?family=Open+Sans:wght@400;600;700&family=Raleway:wght@300;400;600;700&display=swap" rel="stylesheet">
<style>
:root{
  --blue:#1a61c0;
  --blue-deep:#0f4ea6;
  --blue-band:#1763c4;
  --ink:#222;
  --text:#333;
  --muted:#8a8a8a;
  --footer:#1d1d1d;
  --white:#fff;
}
*{margin:0;padding:0;box-sizing:border-box}
html,body{width:1200px;height:2643px;overflow:hidden}
body{position:relative;background:var(--white);font-family:"Open Sans",Arial,sans-serif;color:var(--text)}
.abs{position:absolute}

/* header */
.site-header{position:absolute;left:0;top:0;width:1200px;height:92px;background:var(--blue)}
.brand-box{position:absolute;left:0;top:0;width:425px;height:92px;background:var(--white)}
.brand{position:absolute;left:162px;top:28px;display:flex;align-items:center;gap:10px}
.brand-mark{width:34px;height:34px;background:var(--blue)}
.brand-name{font-family:"Raleway",sans-serif;font-weight:700;font-size:20px;line-height:18px;color:#1f2a44;text-transform:uppercase;letter-spacing:.5px}
.main-nav{position:absolute;left:425px;top:0;height:92px;display:flex}
.main-nav a{display:block;height:92px;line-height:92px;color:var(--white);font-size:13px;text-decoration:none;text-transform:uppercase;padding:0 22px}
.main-nav a.active{background:var(--blue-deep);width:95px;text-align:center;padding:0}
.main-nav a+a{margin-left:0}
.nav-icons{position:absolute;left:1002px;top:38px;display:flex;gap:12px}

/* hero */
.hero{position:absolute;left:0;top:92px;width:1200px;height:549px;background:linear-gradient(90deg,#6b5f66 0%,#a59aa0 20%,#cfc8c2 45%,#b9b2b6 65%,#7d7480 100%)}
.hero-floor{position:absolute;left:0;bottom:0;width:1200px;height:110px;background:linear-gradient(180deg,#b8a89a,#9c8c7c)}
.hero-title{position:absolute;left:0;width:1200px;top:183px;text-align:center;font-family:"Raleway",sans-serif;font-weight:300;font-size:50px;color:var(--white)}
.hero-sub{position:absolute;left:380px;width:440px;top:255px;text-align:center;font-family:"Raleway",sans-serif;font-size:18px;line-height:24px;color:#f2f2f2}
.hero-btn{position:absolute;left:537px;top:326px;width:124px;height:37px;border:1px solid #fff;color:#fff;font-size:11px;font-weight:600;display:flex;align-items:center;justify-content:center;gap:5px}
.hero-arrow{position:absolute;top:258px;width:32px;height:32px;border:1.5px solid #fff;border-radius:50%}

/* headings */
.section-title{position:absolute;left:0;width:1200px;text-align:center;font-family:"Raleway",sans-serif;font-weight:600;font-size:24px;color:var(--ink)}
.section-title span{color:var(--blue)}
.intro{position:absolute;left:212px;width:776px;text-align:center;font-size:11px;line-height:18px;color:var(--text)}

/* features */
.feature{position:absolute;top:800px;width:200px;text-align:center}
.feature svg{display:block;margin:0 auto}
.feature h3{font-size:13px;font-weight:600;color:var(--ink);margin-top:20px}
.feature p{font-size:11px;line-height:18px;margin-top:10px}

/* bands */
.band-panel{position:absolute;background:linear-gradient(135deg,var(--blue-band),#0e55b3)}
.band-photo{position:absolute}
.band-title{position:absolute;font-family:"Raleway",sans-serif;font-weight:600;font-size:22px;line-height:30px;color:#fff}
.band-text{position:absolute;font-size:11.5px;line-height:20px;color:#e8effa}

/* works */
.work{position:absolute;top:1536px;width:280px;height:247px}

/* partners */
.partners{position:absolute;left:162px;top:2290px;width:880px;display:flex;justify-content:space-between;align-items:center}
.partner{display:flex;align-items:center;gap:7px;font-family:"Open Sans",sans-serif;font-weight:600;font-size:19px;color:var(--muted)}
.partner i{display:block;width:22px;height:22px;background:var(--muted)}
.partner i.round{border-radius:50%}

/* footer */
.site-footer{position:absolute;left:0;top:2370px;width:1200px;height:222px;background:var(--footer)}
.footer-brand{position:absolute;left:162px;top:72px;display:flex;align-items:center;gap:10px}
.footer-brand .brand-mark{background:var(--white)}
.footer-brand .brand-name{color:var(--white)}
.socials{position:absolute;left:162px;top:128px;display:flex;gap:6px}
.socials span{width:26px;height:26px;border:1.5px solid #fff;border-radius:50%}
.footer-col{position:absolute;top:36px;color:#fff}
.footer-col h4{font-family:"Raleway",sans-serif;font-weight:700;font-size:15px;margin-bottom:12px;letter-spacing:.3px}
.footer-col ul{list-style:none;font-size:11.5px;line-height:22px}
.contact-list li{display:flex;gap:10px;align-items:flex-start;line-height:20px}
.contact-list svg{flex:none;margin-top:5px}
.news-note{font-size:11.5px}
.news-form{display:flex;margin-top:12px}
.news-input{width:162px;height:36px;background:#fff;color:#888;font-size:11px;font-style:italic;line-height:36px;padding-left:10px}
.news-btn{width:78px;height:36px;background:var(--blue);color:#fff;font-size:12px;font-weight:700;line-height:36px;text-align:center}
.copy-bar{position:absolute;left:0;top:2592px;width:1200px;height:51px;background:var(--blue);color:#fff;font-size:11px;line-height:51px;text-align:center}
</style>
</head>
<body>

<header class="site-header">
  <div class="brand-box">
    <div class="brand"><span class="brand-mark"></span><span class="brand-name">Vantage<br>Interiors</span></div>
  </div>
  <nav class="main-nav">
    <a class="active" href="#">Home</a>
    <a href="#">Services</a>
    <a href="#">Products</a>
    <a href="#">Gallery</a>
    <a href="#">Contact Us</a>
  </nav>
  <div class="nav-icons">
    <svg width="12" height="12" viewBox="0 0 12 12"><circle cx="5" cy="5" r="3.5" fill="none" stroke="#fff" stroke-width="1.6"/><line x1="7.5" y1="7.5" x2="11" y2="11" stroke="#fff" stroke-width="1.8"/></svg>
    <svg width="11" height="12" viewBox="0 0 11 12"><circle cx="5.5" cy="3.5" r="3" fill="#fff"/><path d="M0 12c0-4 2.5-5.5 5.5-5.5S11 8 11 12z" fill="#fff"/></svg>
  </div>
</header>

<section class="hero" role="img" aria-label="Photo of a bright living room with concrete feature wall, white sofa and tall windows">
  <div class="hero-floor"></div>
  <h1 class="hero-title">Vantage Interiors</h1>
  <p class="hero-sub">Sed ut perspiciatis unde omnis iste sit voluptatem accusantium doloremque laudantium rap</p>
  <div class="hero-btn">READ MORE
    <svg width="10" height="10" viewBox="0 0 10 10"><circle cx="5" cy="5" r="5" fill="#fff"/><path d="M4 2.8 6.2 5 4 7.2" fill="none" stroke="#8a8088" stroke-width="1.4"/></svg>
  </div>
  <div class="hero-arrow" style="left:40px"><svg width="29" height="29" viewBox="0 0 29 29"><path d="M16.5 9.5 11.5 14.5 16.5 19.5" fill="none" stroke="#fff" stroke-width="1.6"/></svg></div>
  <div class="hero-arrow" style="left:1120px"><svg width="29" height="29" viewBox="0 0 29 29"><path d="M12.5 9.5 17.5 14.5 12.5 19.5" fill="none" stroke="#fff" stroke-width="1.6"/></svg></div>
</section>

<h2 class="section-title" style="top:668px"><span>Welcome</span> to Vantage Interiors</h2>
<p class="intro" style="top:718px">Lorem ipsum dolor sit amet, consectetur adipiscing elit, sed do eiusmod tempor incididunt ut labore et dolore magna aliqua. Ut enim ad minim veniam, quis nostrud ipsum dolor sit amet, consectetur adipiscing elit, sed do eiusmod tempor incididunt ut labore et dolore magna aliquat enim ad minim.</p>

<div class="feature" style="left:155px">
  <svg width="78" height="58" viewBox="0 0 78 58"><path d="M22 20 39 12 56 20 39 28z" fill="#1a61c0"/><path d="M22 20v20l17 8V28z" fill="#1a61c0"/><path d="M56 20v20l-17 8V28z" fill="#3d7fd3"/><ellipse cx="39" cy="32" rx="34" ry="12" fill="none" stroke="#1a61c0" stroke-width="3"/></svg>
  <h3>Supply</h3>
  <p>Lorem ipsum dolor sit amet, consur adipiscing elit, sed do eiusmod tempin cididunt ut labore et dolore ma.</p>
</div>
<div class="feature" style="left:385px">
  <svg width="78" height="58" viewBox="0 0 78 58"><line x1="24" y1="8" x2="56" y2="50" stroke="#1a61c0" stroke-width="6" stroke-linecap="round"/><circle cx="24" cy="10" r="8" fill="none" stroke="#1a61c0" stroke-width="4"/><line x1="56" y1="8" x2="24" y2="50" stroke="#1a61c0" stroke-width="5" stroke-linecap="round"/><rect x="50" y="4" width="10" height="8" fill="#1a61c0"/></svg>
  <h3>Install decorative</h3>
  <p>Lorem ipsum dolor sit amet, consur adipiscing elit, sed do eiusmod tempin cididunt ut labore et dolore ma.</p>
</div>
<div class="feature" style="left:587px">
  <svg width="78" height="58" viewBox="0 0 78 58"><rect x="16" y="4" width="26" height="20" fill="none" stroke="#1a61c0" stroke-width="3"/><rect x="26" y="24" width="6" height="6" fill="#1a61c0"/><rect x="10" y="30" width="58" height="5" fill="#1a61c0"/><rect x="12" y="35" width="4" height="20" fill="#1a61c0"/><rect x="48" y="35" width="18" height="20" fill="none" stroke="#1a61c0" stroke-width="3"/><line x1="48" y1="45" x2="66" y2="45" stroke="#1a61c0" stroke-width="2"/><rect x="54" y="16" width="10" height="14" fill="#1a61c0"/></svg>
  <h3>Printed films for Office</h3>
  <p>Lorem ipsum dolor sit amet, consur adipiscing elit, sed do eiusmod tempin cididunt ut labore et dolore ma.</p>
</div>
<div class="feature" style="left:848px">
  <svg width="78" height="58" viewBox="0 0 78 58"><path d="M39 4 68 28H60V54H18V28H10z" fill="none" stroke="#1a61c0" stroke-width="4" stroke-linejoin="round"/><path d="M27 40 39 30 51 40z" fill="#1a61c0"/><rect x="30" y="40" width="18" height="8" fill="#1a61c0"/></svg>
  <h3>Home decoration</h3>
  <p>Lorem ipsum dolor sit amet, consur adipiscing elit, sed do eiusmod tempin cididunt ut labore et dolore ma.</p>
</div>

<div class="band-panel" style="left:0;top:1011px;width:446px;height:381px"></div>
<div class="band-photo" style="left:446px;top:1011px;width:754px;height:381px;background:linear-gradient(135deg,#6f6a66 0%,#b9b4ad 35%,#e4e2de 60%,#9aa0a6 100%)" role="img" aria-label="Photo of a modern kitchen with white dining table and dark chairs"></div>
<h2 class="band-title" style="left:162px;top:1093px">Interior Decoration<br>to Residential</h2>
<p class="band-text" style="left:162px;top:1174px;width:268px">Sed ut perspiciatis unde omnis iste natus err orsi tvoluptatem accusantium doloremuelau dan tiu mtotam remaperiam, eaque ipsaluae abilo invent ore veritatis et quasi architecto beatae vitae dicta sunt explicaboemo enim ipsam voluptatem quia volupt as sit asperm atur aut odit autquia conuitu sit aspern atur aut odit autr.</p>

<h2 class="section-title" style="top:1420px"><span>Our</span> Works</h2>
<p class="intro" style="top:1467px">Lorem ipsum dolor sit amet, consectetur adipiscing elit, sed do eiusmod tempor incididunt ut labore et dolore magna aliqua. Ut enim ad minim veniam, quis nostrud ipsum dolor sit amet, consectetur adipiscing elit, sed do eiusmod tempor incididunt ut labore et dolore magna aliquat enim ad minim.</p>

<div class="work" style="left:162px;background:linear-gradient(135deg,#a89a4c,#c9b78a 45%,#c8412e 90%)" role="img" aria-label="Photo of a striped wooden feature wall with red lounge chairs"></div>
<div class="work" style="left:460px;background:linear-gradient(135deg,#e6e6e2,#9aa19c 55%,#5c635f)" role="img" aria-label="Photo of a bright grey room with pendant lamps and white counter"></div>
<div class="work" style="left:758px;background:linear-gradient(160deg,#6f7c74,#8c9891 55%,#cfcac2)" role="img" aria-label="Photo of a green wall with artwork above a wooden sideboard"></div>

<div class="band-photo" style="left:0;top:1861px;width:754px;height:380px;background:linear-gradient(120deg,#8d8780 0%,#c9c3bb 40%,#e5e1dc 70%,#a9a39c 100%)" role="img" aria-label="Photo of a concrete commercial interior with white lamps and tall windows"></div>
<div class="band-panel" style="left:754px;top:1861px;width:446px;height:380px"></div>
<h2 class="band-title" style="left:781px;top:1941px">Interior Decoration<br>to commercial markets.</h2>
<p class="band-text" style="left:781px;top:2025px;width:268px">Sed ut perspiciatis unde omnis iste natus err orsi tvoluptatem accusantium doloremuelau dan tiu mtotam remaperiam, eaque ipsaluae abilo invent ore veritatis et quasi architecto beatae vitae dicta sunt explicaboemo enim ipsam voluptatem quia volupt as sit asperm atur aut odit autquia conuitu sit aspern atur aut odit autr.</p>

<div class="partners">
  <div class="partner"><i class="round"></i>Northlake</div>
  <div class="partner"><i></i>Brightmill</div>
  <div class="partner">Quillpost</div>
  <div class="partner">stockpine</div>
  <div class="partner"><i></i>Tilework</div>
  <div class="partner"><i class="round"></i>Harborly</div>
</div>

<footer class="site-footer">
  <div class="footer-brand"><span class="brand-mark"></span><span class="brand-name">Vantage<br>Interiors</span></div>
  <div class="socials"><span></span><span></span><span></span><span></span><span></span></div>
  <div class="footer-col" style="left:428px">
    <h4>LINKS</h4>
    <ul><li>Home</li><li>Services</li><li>Products</li><li>Gallery</li><li>Contact us</li></ul>
  </div>
  <div class="footer-col" style="left:581px;width:180px">
    <h4>CONTACT US</h4>
    <ul class="contact-list">
      <li><svg width="9" height="11" viewBox="0 0 9 11"><path d="M4.5 0A4 4 0 0 1 8.5 4c0 3-4 7-4 7S.5 7 .5 4a4 4 0 0 1 4-4z" fill="#fff"/><circle cx="4.5" cy="4" r="1.5" fill="#1d1d1d"/></svg><span>Postal address: PO Box 218, Elm Ridge street line</span></li>
      <li><svg width="10" height="10" viewBox="0 0 10 10"><path d="M2 0 4 2.5 3 4a6 6 0 0 0 3 3l1.5-1L10 8 8.5 10C4 10 0 6 0 1.5z" fill="#fff"/></svg><span>Phone: 415-302-7716</span></li>
      <li><svg width="10" height="10" viewBox="0 0 10 10"><rect x="2" y="0" width="6" height="3" fill="#fff"/><rect x="0" y="3.5" width="10" height="4.5" fill="#fff"/><rect x="2" y="7" width="6" height="3" fill="#fff"/></svg><span>Fax: 415-302-7717</span></li>
      <li><svg width="10" height="8" viewBox="0 0 10 8"><rect width="10" height="8" fill="#fff"/><path d="M0 0 5 4.5 10 0" fill="none" stroke="#1d1d1d" stroke-width="1"/></svg><span>hello@vantageinteriors.com</span></li>
    </ul>
  </div>
  <div class="footer-col" style="left:795px">
    <h4>SIGN UP NEWSLETTER</h4>
    <p class="news-note">Please sign up here for latest deals</p>
    <div class="news-form"><div class="news-input">Email address</div><div class="news-btn">SIGN UP</div></div>
  </div>
</footer>

<div class="copy-bar">© 2016 Vantage Interiors.&nbsp; All Copyrights are reserved&nbsp; Term of Use. Privacy Policy</div>

</body>
</html>
```